Bridgeway Health of Nations

Please design a business card that is colorful but at the same time easy to read. We are based out on Miami Florida. We are a small start up healthcare company that has been in operation for 1 year. Our clients are Hospitals, Insurance companies, and Manage Care health companies. We are growing quickly and lead the niche we are in. Please make the card 2 sided on the front will be the typical info. Logo, Company Name, Persons Name, Title, Cell #, Office #, Fax#, email, website. No address. On the back we will list 5 services that we do. For example Care Transitions, Case management, Risk assessment, Utilization Review.
Target Market(s)
CEO's and COO's of hospitals and healthcare companies.
Industry/Entity Type
Healthcare

```html
<!DOCTYPE html>
<html lang="en">
<head>
<meta charset="utf-8">
<title>Bridgeway Health of Nations – Business Card</title>
<link href="https://fonts.googleapis.com/css2?family=Signika:wght@300;400;600;700&display=swap" rel="stylesheet">
<style>
  :root {
    --backdrop: #1d1d1f;
    --paper: #f3f3f1;
    --ink-dark: #454545;
    --brand-blue: #2c4a9a;
    --brand-green: #16a34a;
    --brand-yellow: #d9c81a;
    --brand-red: #d42f2a;
    --band-blue: #2d4c9b;
    --band-green: #12a34b;
    --band-yellow: #e6dc32;
    --band-red: #d0332b;
    --panel-top: #35358a;
    --panel-bottom: #2f90cf;
    --panel-text: #ffffff;
  }
  * { margin: 0; padding: 0; box-sizing: border-box; }
  html, body {
    width: 1200px; height: 896px; overflow: hidden;
    background: var(--backdrop);
    font-family: "Signika", sans-serif;
  }
  .stage { position: relative; width: 1200px; height: 896px; }
  .card {
    position: absolute; top: 181px;
    width: 297px; height: 533px;
    border-radius: 22px; overflow: hidden;
    background: var(--paper);
  }
  .card--back { left: 281px; }
  .card--front { left: 628px; }

  /* back side */
  .back-brand {
    position: absolute; left: 0; right: 0; top: 86px;
    text-align: center;
  }
  .back-brand .mark-dot {
    display: block; margin: 0 auto 14px;
    width: 54px; height: 54px; border-radius: 50%;
    background: var(--brand-blue);
  }
  .back-brand .brand-name {
    font-size: 24px; font-weight: 600; line-height: 1.15;
    color: var(--brand-blue);
  }
  .services {
    position: absolute; left: 70px; top: 302px;
    list-style: none;
  }
  .services li {
    display: flex; align-items: center;
    height: 30px; font-size: 15.5px; font-weight: 600;
  }
  .services li::before {
    content: ""; width: 9px; height: 9px; margin-right: 6px;
    background: currentColor;
  }
  .services .svc-blue { color: var(--brand-blue); }
  .services .svc-green { color: var(--brand-green); }
  .services .svc-yellow { color: var(--brand-yellow); }
  .services .svc-red { color: var(--brand-red); }
  .color-bands {
    position: absolute; left: 0; right: 0; bottom: 0; height: 30px;
    display: flex;
  }
  .color-bands span { flex: 1; }
  .color-bands .b1 { background: var(--band-blue); }
  .color-bands .b2 { background: var(--band-green); }
  .color-bands .b3 { background: var(--band-yellow); }
  .color-bands .b4 { background: var(--band-red); }

  /* front side */
  .front-brand {
    position: absolute; left: 22px; top: 64px;
    display: flex; align-items: center; gap: 18px;
  }
  .front-brand .mark-dot {
    width: 70px; height: 70px; border-radius: 50%;
    background: var(--brand-blue); flex: none;
  }
  .front-brand .brand-name {
    font-size: 25px; font-weight: 600; line-height: 1.16;
    color: var(--ink-dark);
  }
  .contact-panel {
    position: absolute; left: 0; right: 0; top: 247px; bottom: 0;
    background: linear-gradient(180deg, var(--panel-top) 0%, var(--panel-bottom) 100%);
    color: var(--panel-text);
  }
  .person-name {
    position: absolute; left: 56px; top: 38px;
    font-size: 22px; font-weight: 300; letter-spacing: 0.3px;
  }
  .person-title {
    position: absolute; left: 56px; top: 65px;
    font-size: 13.5px; font-weight: 300;
  }
  .contact-list {
    position: absolute; left: 56px; top: 115px; list-style: none;
  }
  .contact-list li {
    display: flex; align-items: center; height: 20.3px;
    font-size: 14px; font-weight: 300; letter-spacing: 0.2px;
  }
  .contact-list svg { width: 12px; height: 12px; margin-right: 16px; fill: var(--panel-text); }
  .website {
    position: absolute; left: 56px; top: 229px;
    font-size: 13.5px; font-weight: 600; letter-spacing: 0.9px;
  }
</style>
</head>
<body>
<main class="stage">

  <section class="card card--back" aria-label="Business card, services side">
    <div class="back-brand">
      <span class="mark-dot"></span>
      <p class="brand-name">Bridgeway Health<br>of Nations</p>
    </div>
    <ul class="services">
      <li class="svc-blue">Care Transitions</li>
      <li class="svc-green">Case management</li>
      <li class="svc-yellow">Risk assessment</li>
      <li class="svc-red">Utilization Review</li>
    </ul>
    <div class="color-bands"><span class="b1"></span><span class="b2"></span><span class="b3"></span><span class="b4"></span></div>
  </section>

  <section class="card card--front" aria-label="Business card, contact side">
    <div class="front-brand">
      <span class="mark-dot"></span>
      <p class="brand-name">Bridgeway<br>Health of<br>Nations</p>
    </div>
    <div class="contact-panel">
      <h1 class="person-name">MARCUS DELANEY</h1>
      <p class="person-title">Operation Manager</p>
      <ul class="contact-list">
        <li><svg viewBox="0 0 12 12" aria-hidden="true"><path d="M2.2 0.8l2 2-1 1.4c.7 1.5 1.8 2.6 3.3 3.3l1.4-1 2 2-1.3 1.8C5 10 2 7 .4 2.1z"/></svg>(305) 41 620 18 47</li>
        <li><svg viewBox="0 0 12 12" aria-hidden="true"><path d="M3 0h6v12H3zM4 1.5v7.5h4V1.5zM5.5 10h1v1h-1z" fill-rule="evenodd"/></svg>(305) 82 514 36 09</li>
        <li><svg viewBox="0 0 12 12" aria-hidden="true"><path d="M3 0h6v3H3zM0 4h12v5H9.5v3h-7V9H0zM3.5 8v3h5V8z" fill-rule="evenodd"/></svg>(305) 41 620 18 52</li>
        <li><svg viewBox="0 0 12 12" aria-hidden="true"><path d="M0 4l6-4 6 4v7H0zM1.2 4.4L6 7.6l4.8-3.2L6 1.3z" fill-rule="evenodd"/></svg>marcus@bridgewayhealth.com</li>
      </ul>
      <p class="website">www.bridgewayhealth.com</p>
    </div>
  </section>

</main>
</body>
</html>
```